Foot and ankle surgeon requires a website design

I need a website where prospective and established patients can obtain information and then direct them to making appointments. My practice is a highly professional surgical practice specialising in surgery to the foot and ankle. My title is Mr Colin Brasket, Podiatric Foot & Ankle Surgeon. My qualifications are: BSc MSc FACPS
The practice website will require information on: Locations, phone numbers to make appointments, general background on podiatric surgery,
I would like to include information on: my hospital appointments, surgical fellowships held, training programs undertaken, association memberships, publications written, links to useful websites
A page dedicated to common foot conditions would be useful and also a page with referral information including an online registration section that will be sent direct to the receptionist.
Examples of similar websites include:
http://www.dorvelquintaro.com.au/
http://www.haldenfootsurgeon.com.au/
I will provide files on logo, self photos and my personal training history etc.
Also if there is going to be a background theme I personally am associated with surfing and beach activities, it would be great if this was able to be reflected in the design.
Thank you.

```html
<!DOCTYPE html>
<html lang="en">
<head>
<meta charset="utf-8">
<title>Mr Colin Brasket – Podiatric Foot &amp; Ankle Surgeon</title>
<link href="https://fonts.googleapis.com/css2?family=PT+Sans:wght@400;700&family=PT+Sans+Narrow:wght@400;700&display=swap" rel="stylesheet">
<style>
:root{
  --blue:#0b4f94;
  --blue-dark:#063b73;
  --orange:#e27a12;
  --ink:#222;
  --text:#3a3a3a;
  --panel:#f6f6f6;
  --line:#d8d8d8;
  --band:#ececec;
  --footer:#2b2b2b;
}
*{margin:0;padding:0;box-sizing:border-box}
html,body{width:978px;height:1200px;overflow:hidden;background:#fff}
body{position:relative;font-family:"PT Sans",sans-serif;color:var(--text)}
.abs{position:absolute}

/* header */
.brand{left:186px;top:36px;display:flex;align-items:center;gap:10px}
.brand-dot{width:34px;height:34px;border-radius:50%;background:var(--blue)}
.brand-name{font-weight:700;font-size:16px;color:var(--blue-dark);line-height:1}
.brand-tag{font-size:8px;color:var(--orange);margin-top:3px}
.social{left:487px;top:35px;display:flex;gap:3px}
.social span{width:25px;height:25px;background:#b8b8b8;display:block}
.appt{left:617px;top:21px;width:175px;height:53px;border:1px solid #ddd;border-radius:4px;background:linear-gradient(#fafafa,#ececec);display:flex;align-items:center;padding-left:8px;gap:9px}
.appt-label{font-size:10.5px;color:#333;font-family:"PT Sans Narrow",sans-serif}
.appt-phone{font-size:15px;font-weight:700;color:var(--blue-dark);margin-top:1px}

/* nav */
.nav{left:169px;top:99px;width:640px;height:42px;background:var(--blue);display:flex;align-items:center;justify-content:space-between;padding:0 15px 0 17px}
.nav a{font-family:"PT Sans Narrow",sans-serif;color:#fff;font-size:11px;line-height:1;white-space:nowrap;text-decoration:none;text-transform:uppercase;position:relative}
.nav a.active::after{content:"";position:absolute;left:50%;bottom:-20px;transform:translateX(-50%);border:5px solid transparent;border-bottom-color:var(--orange)}

/* hero */
.hero{left:169px;top:154px;width:640px;height:253px;background:
  linear-gradient(180deg,rgba(0,0,0,0) 45%,rgba(120,60,50,.35) 100%),
  radial-gradient(ellipse 45% 40% at 58% 30%,#f2b27a 0%,rgba(230,150,90,0) 100%),
  linear-gradient(90deg,#3f3a22 0%,#7a5a35 22%,#c27b4d 50%,#7a5a35 78%,#3f3a22 100%)}
.hero-caption{left:169px;top:364px;width:640px;height:43px;background:rgba(30,30,40,.45);display:flex;align-items:center;justify-content:center}
.hero-caption h1{font-family:"PT Sans Narrow",sans-serif;font-weight:700;color:#fff;font-size:24px;letter-spacing:.2px}
.arrow{top:377px}

/* feature boxes */
.feature{top:422px;width:202px;height:202px;background:var(--panel);border:1px solid #e0e0e0}
.feature-head{height:35px;background:linear-gradient(var(--blue),var(--blue-dark));color:#fff;font-size:12px;display:flex;align-items:center;justify-content:center;text-transform:uppercase;margin:-1px -1px 0}
.feature-img{position:absolute;left:16px;top:54px;width:169px;height:112px}
.feature-more{position:absolute;left:0;right:0;top:180px;text-align:center;font-size:12px;color:#444}

/* welcome */
.h2{font-size:17px;font-weight:700;color:var(--ink)}
.body-text{font-size:8.3px;line-height:14.4px;color:#333}
.justify{text-align:justify}

/* news */
.news-date{left:577px;width:46px;height:38px;background:#eee;text-align:center}
.news-date .day{font-weight:700;font-size:11.5px;color:#333;height:19px;line-height:21px}
.news-date .month{background:var(--blue);color:#fff;font-weight:700;font-size:9px;height:19px;line-height:19px}
.news-item{left:642px;width:166px}
.news-title{font-size:8.4px;color:var(--blue);margin-bottom:1px;line-height:12px}
.news-item p{font-size:8px;line-height:13px;text-align:justify}
.divider{left:577px;width:231px;height:1px;background:var(--line)}

/* locations */
.locations{left:0;top:912px;width:978px;height:216px;background:var(--band)}
.loc{top:990px}
.loc-title{font-size:13.5px;color:var(--orange);margin-bottom:3px}
.loc p{font-size:10px;line-height:17px;color:#333}
.loc svg{position:absolute;left:-14px;top:0}
.map{left:624px;top:984px;width:186px;height:96px;background:radial-gradient(ellipse at 30% 40%,#9a9a9a 0%,rgba(180,180,180,0) 45%),radial-gradient(ellipse at 72% 45%,#999 0%,rgba(180,180,180,0) 50%)}

/* footer */
.footer{left:0;top:1128px;width:978px;height:72px;background:var(--footer);color:#fff;text-align:center}
.footer-links{margin-top:19px;font-size:8.8px}
.footer-links a{color:#fff;text-decoration:none}
.footer-links span{margin:0 7px}
.footer-copy{margin-top:11px;font-size:8.8px}
</style>
</head>
<body>

<header>
  <div class="abs brand">
    <span class="brand-dot"></span>
    <div>
      <div class="brand-name">Mr Colin Brasket</div>
      <div class="brand-tag">Podiatric Foot &amp; Ankle Surgeon</div>
    </div>
  </div>
  <div class="abs social" aria-label="Social links"><span></span><span></span><span></span><span></span></div>
  <div class="abs appt">
    <svg width="38" height="38" viewBox="0 0 38 38" aria-hidden="true">
      <circle cx="19" cy="19" r="17" fill="none" stroke="var(--orange)" stroke-width="2.5"/>
      <path d="M13 11c1.5-1 3-1 3.5.5l1.2 3c.3.8 0 1.5-.7 2l-1 .8c.8 2 2.4 3.7 4.4 4.6l.8-1c.5-.7 1.3-.9 2-.6l3 1.3c1.4.6 1.3 2.2.3 3.6-1.3 1.7-3.4 2-5.6 1-4-1.8-7-5-8.6-9-.8-2.2-.5-4.6.7-6.2z" fill="var(--orange)"/>
    </svg>
    <div>
      <div class="appt-label">MAKE AN APPOINTMENT</div>
      <div class="appt-phone">08 9412 7706</div>
    </div>
  </div>
</header>

<nav class="abs nav">
  <a class="active" href="#">Home</a>
  <a href="#">Appointments</a>
  <a href="#">Surgical Fellowships</a>
  <a href="#">Training Programs</a>
  <a href="#">Memberships</a>
  <a href="#">Publications</a>
  <a href="#">Useful Websites</a>
  <a href="#">Contact Us</a>
</nav>

<div class="abs hero" role="img" aria-label="Runner on a sunlit tree-lined road at sunset"></div>
<div class="abs hero-caption"><h1>Relieve your pain and get back in the game!</h1></div>
<svg class="abs arrow" style="left:214px" width="15" height="15" viewBox="0 0 15 15" aria-hidden="true"><circle cx="7.5" cy="7.5" r="6.3" fill="none" stroke="#fff" stroke-width="1.6"/><path d="M9 4.5 6 7.5 9 10.5" fill="none" stroke="#fff" stroke-width="1.8"/></svg>
<svg class="abs arrow" style="left:743px" width="15" height="15" viewBox="0 0 15 15" aria-hidden="true"><circle cx="7.5" cy="7.5" r="6.3" fill="none" stroke="#fff" stroke-width="1.6"/><path d="M6 4.5 9 7.5 6 10.5" fill="none" stroke="#fff" stroke-width="1.8"/></svg>

<section>
  <div class="abs feature" style="left:171px">
    <div class="feature-head">Appointments</div>
    <div class="feature-img" role="img" aria-label="Stethoscope and pen on a calendar" style="background:radial-gradient(ellipse at 35% 30%,#eef0f5 0%,#c3c8d4 45%,#8f97a8 100%)"></div>
    <div class="feature-more">More</div>
  </div>
  <div class="abs feature" style="left:389px">
    <div class="feature-head">Surgical Fellowships</div>
    <div class="feature-img" role="img" aria-label="Clinician examining a patient's foot in a clinic" style="background:radial-gradient(ellipse at 55% 55%,#c9a58e 0%,#6e7f95 45%,#3d4a5e 100%)"></div>
    <div class="feature-more">More</div>
  </div>
  <div class="abs feature" style="left:606px">
    <div class="feature-head">Training Programs</div>
    <div class="feature-img" role="img" aria-label="Gloved practitioner treating a foot" style="background:linear-gradient(90deg,#f1f2f4 0%,#dfe2e6 35%,#7fa6d6 50%,#d8c07a 68%,#c9a33f 100%)"></div>
    <div class="feature-more">More</div>
  </div>
</section>

<section>
  <h2 class="abs h2" style="left:168px;top:648px">Welcome to Colin Brasket</h2>
  <div class="abs" role="img" aria-label="Hands holding a sore foot" style="left:169px;top:690px;width:176px;height:110px;background:radial-gradient(ellipse at 45% 55%,#d8b9a8 0%,#5aa9d8 40%,#1b7fc0 75%,#0f5f98 100%)"></div>
  <p class="abs body-text justify" style="left:358px;top:686px;width:189px">The Heel and Stride Care Group strive to provide exceptional service and care to all patients, young and old, to ensure they enjoy a pain free lifestyle. For those unfamiliar with our services, we are a team of accredited health professionals dealing with the prevention, diagnosis, treatment and rehabilitation of medical and surgical conditions related to feet, ankles and lower limbs.</p>
  <p class="abs body-text" style="left:169px;top:814px;width:380px">The Heel and Stride Care Group have practices based throughout regional Western Australia in Coralport and Redgum Flat and offer the following services; sports injuries, foot care, foot orthoses and diabetes care. Many foot and lower limb problems, if identified early can be prevented, so take the right step and contact the Heel and Stride Care Group for advice on your foot, ankle, heel or leg pain or sports injury.</p>
</section>

<section>
  <h2 class="abs h2" style="left:574px;top:648px">Latest News</h2>
  <div class="abs news-date" style="top:691px"><div class="day">30</div><div class="month">JULY</div></div>
  <div class="abs news-item" style="top:688px">
    <div class="news-title">Magna non nunc tristique rhoncuseri</div>
    <p>Facilisis consequat. Curabitur vel lorem sit amet nulla ullamcorper fermentum. In vitae varius augue, eu consectetur ligula. Etiam dui eros, laoreet sit amet est</p>
  </div>
  <div class="abs divider" style="top:775px"></div>
  <div class="abs news-date" style="top:803px"><div class="day">28</div><div class="month">JULY</div></div>
  <div class="abs news-item" style="top:800px">
    <div class="news-title">Tagna non nunc tristique rhoncuserr</div>
    <p>Donec laoreet metus id laoreet malesuada. Lorem ipsum dolor sit amet, consectetur adipiscing elit. Nullam consectetur orci sed null</p>
  </div>
</section>

<section>
  <div class="abs locations">
    <svg width="978" height="6" viewBox="0 0 978 6" preserveAspectRatio="none" style="position:absolute;top:-5px;left:0" aria-hidden="true">
      <pattern id="zig" width="6" height="6" patternUnits="userSpaceOnUse"><path d="M0 6 3 1 6 6z" fill="var(--band)"/></pattern>
      <rect width="978" height="6" fill="url(#zig)"/>
    </svg>
  </div>
  <h2 class="abs h2" style="left:171px;top:936px">Our Locations</h2>

  <div class="abs loc" style="left:183px">
    <svg width="11" height="15" viewBox="0 0 11 15" aria-hidden="true"><path d="M5.5 0A5.5 5.5 0 0 0 0 5.5C0 9.5 5.5 15 5.5 15S11 9.5 11 5.5A5.5 5.5 0 0 0 5.5 0z" fill="var(--blue)"/><circle cx="5.5" cy="5.5" r="2" fill="#fff"/></svg>
    <div class="loc-title">Coralport</div>
    <p>48 Seabreeze Parade,<br>PO BOX 2841,<br>Coralport WA 6612<br>Ph: 08 9412 7706<br>Fax: 08 9412 7790</p>
  </div>
  <div class="abs loc" style="left:354px">
    <svg width="11" height="15" viewBox="0 0 11 15" aria-hidden="true"><path d="M5.5 0A5.5 5.5 0 0 0 0 5.5C0 9.5 5.5 15 5.5 15S11 9.5 11 5.5A5.5 5.5 0 0 0 5.5 0z" fill="var(--blue)"/><circle cx="5.5" cy="5.5" r="2" fill="#fff"/></svg>
    <div class="loc-title">West End, Coralport</div>
    <p>7A &amp; 7B Tidewater Street,<br>Coralport 6612.<br>Ph: 9412 6630<br>Fax: 9412 6631</p>
  </div>
  <div class="abs loc" style="left:527px">
    <svg width="11" height="15" viewBox="0 0 11 15" aria-hidden="true"><path d="M5.5 0A5.5 5.5 0 0 0 0 5.5C0 9.5 5.5 15 5.5 15S11 9.5 11 5.5A5.5 5.5 0 0 0 5.5 0z" fill="var(--blue)"/><circle cx="5.5" cy="5.5" r="2" fill="#fff"/></svg>
    <div class="loc-title">Redgum Flat</div>
    <p>3/14 Harbourline St,<br>Redgum Flat WA 6475<br>Ph: 08 9076 2215<br>Fax: 08 9076 2219</p>
  </div>
  <div class="abs map" role="img" aria-label="Grey world map with location markers"></div>
</section>

<footer class="abs footer">
  <div class="footer-links">
    <a href="#">Home</a><span>|</span><a href="#">Appointments</a><span>|</span><a href="#">Surgical fellowships</a><span>|</span><a href="#">Training programs</a><span>|</span><a href="#">Memberships</a><span>|</span><a href="#">Publications</a><span>|</span><a href="#">Useful websites</a><span>|</span><a href="#">Contact us</a>
  </div>
  <div class="footer-copy">Copy right © 2014 &nbsp;|&nbsp; Privacy Policy</div>
</footer>

</body>
</html>
```